Software Product Flyer Design

A established czech software company needs a marketing flyer to promote their software product and its modules.
The overall feel of the flyer must to be serious, but also eye-catching, enticing, clever and bold to attract customers.
Unifying graphic element is the new product logo.
The flyer would be A4, colour both sides and folded once (to give 4 pages of A5).
Title page - product logo with module name and module icon, short presentation of the product and list of its key features.
Inside pages - detailed informations with screenshots or graphical schemas.
Back side - informations about technical requirements and user support, contacts (address, phone, fax, e-mail, web pages - no social networks).
Product logo, module icon and some images attached.
Updates
Hello,
Reason: For organizational reasons we extending the deadline by 10 days.
FYI: We have uploaded the new ZIP file with previous version of our flyer.
Attached PDF file with text for inner pages.
Target Market(s)
Existing or new customers like municipalities, public authorities and nonprofit organizations.
Industry/Entity Type
Marketing
Requirements
Must have
- Winning designer must provide a template for Adobe InDesign based on his graphic design.
Avoid to using exotic fonts - in Czech we use Latin Extended characters (like áéěíýůčřžšťďň).
Nice to have
- Using graphic motif from product logo like as attached splash screen.

```html
<!DOCTYPE html>
<html lang="cs">
<head>
<meta charset="utf-8">
<title>Veranta Majetek – leták</title>
<link rel="stylesheet" href="https://fonts.googleapis.com/css2?family=Open+Sans:ital,wght@0,400;0,600;0,700;1,400&family=Arimo:wght@700&family=PT+Serif&display=swap">
<style>
  :root{
    --ink:#3d4249;
    --ink-deep:#33373d;
    --orange:#e8501a;
    --orange-soft:#f07a3c;
    --paper:#ffffff;
    --paper-grey:#dcdcdc;
    --label-grey:#6b6f75;
    --text:#2f3237;
    --stage:#ebe8e3;
  }
  *{box-sizing:border-box;margin:0;padding:0}
  html,body{width:1200px;height:1200px;overflow:hidden}
  body{background:var(--stage);font-family:"Open Sans",Arial,sans-serif;color:var(--text)}
  .spread{position:absolute;left:40px;top:204px;width:1120px;height:792px;display:flex;box-shadow:0 10px 30px rgba(0,0,0,.25)}
  .page{position:relative;width:560px;height:792px;display:flex;flex-direction:column;overflow:hidden}
  .page--back{background:var(--paper)}
  .page--front{background:linear-gradient(180deg,#fff 0%,#f3f3f3 55%,var(--paper-grey) 100%);border-left:1px solid #c9c9c9}

  /* back page */
  .tech{background:var(--ink);color:#fff;padding:14px 22px 16px;height:232px}
  .tech__title{font-size:20px;font-weight:600}
  .tech__intro{font-size:10px;font-style:italic;margin:4px 0 12px;line-height:1.35;color:#e6e6e6}
  .server{display:flex;gap:0;align-items:stretch}
  .server__shot{width:150px;height:128px;background:linear-gradient(160deg,#fafafa,#cfd3d8)}
  .server__tab{width:26px;height:128px;background:var(--orange);display:flex;align-items:center;justify-content:center}
  .server__tab span{writing-mode:vertical-rl;transform:rotate(180deg);font-weight:700;font-size:13px;letter-spacing:1px}
  .server__list{list-style:none;margin-left:16px;flex:1;font-size:10px;line-height:1.35;display:flex;flex-direction:column;gap:9px;padding-top:4px}
  .bullet-list li{position:relative;padding-left:12px}
  .bullet-list li::before{content:"";position:absolute;left:0;top:5px;width:5px;height:5px;background:currentColor;border-radius:50%}
  .band{background:var(--orange);color:#fff;font-weight:700;font-size:15px;padding:3px 22px;height:26px}
  .workstation{background:var(--ink);color:#fff;padding:10px 22px 14px 40px;height:146px}
  .workstation ul{list-style:none;font-size:10.5px;line-height:1.4}
  .support{flex:1;text-align:center;padding:18px 40px 0;display:flex;flex-direction:column;align-items:center}
  .support__title{color:var(--orange);font-weight:700;font-size:20px}
  .support__lead{font-size:11px;line-height:1.4;margin:6px 0 10px;max-width:440px}
  .support__list{list-style:none;font-size:9.5px;font-style:italic;line-height:1.4;color:#555}
  .brand{display:flex;align-items:center;gap:8px;color:var(--ink);font-weight:700}
  .brand__dot{width:18px;height:18px;border-radius:50%;background:var(--orange)}
  .support .brand{margin-top:20px;font-size:30px}
  .contact{font-size:10px;line-height:1.45;margin-top:10px;color:#444}
  .foot{height:22px;background:var(--orange);border-top:4px solid var(--ink)}

  /* front page */
  .masthead{height:165px;position:relative}
  .masthead .brand{position:absolute;left:40px;top:34px;font-size:46px}
  .masthead .brand__dot{width:26px;height:26px}
  .module{position:absolute;right:22px;top:96px;display:flex;align-items:center;gap:10px}
  .module__icon{width:26px;height:26px;border:2px solid var(--ink);background:#f4f4f4}
  .module__name{font-family:"Arimo",Arial,sans-serif;font-weight:700;font-size:38px;color:var(--ink);position:absolute;right:0;top:30px;white-space:nowrap}
  .front-band{height:16px;background:var(--orange)}
  .screens{background:var(--ink);height:138px;display:flex;gap:12px;padding:20px 16px}
  .screens__item{flex:1;border:3px solid #fff;background:linear-gradient(160deg,#fbfbfb,#c9cfd6)}
  .info{padding:10px 0 0}
  .info__bar{height:24px;background:linear-gradient(90deg,#bfbfbf,#e6e6e6);position:relative}
  .info__label{position:absolute;left:0;top:0;height:24px;width:170px;background:var(--label-grey);color:#fff;font-family:"PT Serif",Georgia,serif;font-size:14px;padding:2px 12px}
  .info__text{font-size:11.5px;line-height:1.45;text-align:justify;padding:10px 26px 8px 40px;color:#333}
  .info__rule{height:18px;background:var(--ink);margin:6px 0 4px}
  .benefits{margin-top:auto;padding:0 0 28px}
  .benefits__head{display:flex;align-items:center;justify-content:center;gap:10px;font-family:"Arimo",Arial,sans-serif;font-weight:700;font-size:19px;color:var(--ink)}
  .benefits__icon{width:22px;height:26px;background:linear-gradient(180deg,#e69a2e,#b5671c);border-radius:3px}
  .benefits__line{height:2px;background:var(--orange);margin:6px 0 6px}
  .benefits__list{list-style:none;font-size:11.5px;line-height:1.4;padding-left:150px}
  .benefits__list li{display:flex;align-items:center;gap:8px}
  .benefits__list svg{width:9px;height:10px;fill:var(--ink)}
  .front-foot{height:12px;background:var(--orange)}
</style>
</head>
<body>
<main class="spread">

  <section class="page page--back">
    <div class="tech">
      <h2 class="tech__title">Technické podmínky</h2>
      <p class="tech__intro">Systém Veranta umožňuje nasazení prakticky u jakéhokoli zákazníka v jakémkoli prostředí bez ohledu na počet uživatelů nebo množství dat.</p>
      <div class="server">
        <div class="server__shot" role="img" aria-label="Snímek obrazovky serverové správy"></div>
        <div class="server__tab"><span>SERVER</span></div>
        <ul class="server__list bullet-list">
          <li>Operační systém Oknix XP a novější nebo operační systém Tuxora</li>
          <li>Systém vyžaduje nainstalovaný runtime pro Kava 1.5, databázi PolarSQL ve verzi 9.2, webový server Tallow Server 7.0 a JMS systém RelayMQ</li>
          <li>Doporučená velikost RAM je minimálně 4 GB</li>
          <li>Minimální diskový prostor je 20 GB</li>
        </ul>
      </div>
    </div>
    <h3 class="band">Pracovní stanice</h3>
    <div class="workstation">
      <ul class="bullet-list">
        <li>Operační systém Oknix XP a novější</li>
        <li>Minimální velikost RAM je 2 GB</li>
        <li>Minimální diskový prostor je 5 GB</li>
        <li>Pro běh programu Veranta na pracovní stanici je zapotřebí runtime pro Kava 1.7 (je součástí instalace)</li>
        <li>Pro zobrazení a tisk sestav je zapotřebí prohlížeč PDF souborů (Ardent Reader 10 nebo jiný)</li>
        <li>Podporované kancelářské balíky: Meridian Office 2007 a novější, FreeDesk Office 3.0 a novější a OpenDesk 3.0 a novější</li>
      </ul>
    </div>
    <div class="support">
      <h3 class="support__title">Uživatelská podpora</h3>
      <p class="support__lead">Společnost Norvik si zakládá na dlouhodobém vztahu se zákazníky, který se podařilo za více než 20 let existence firmy vybudovat.</p>
      <ul class="support__list">
        <li>Regionální zastoupení po celé České republice</li>
        <li>Individuální přístup ke každému zákazníkovi</li>
        <li>Pracovní postupy zpracované formou názorných prezentací</li>
        <li>Tichá aktualizace programů přes internet</li>
        <li>Školení, metodická podpora a telefonické poradenství</li>
        <li>Aktuální informace na webových stránkách</li>
      </ul>
      <div class="brand"><span class="brand__dot"></span>Veranta</div>
      <address class="contact" style="font-style:normal">
        Veranta Ltd<br>
        170 Mine St., Country, Address Line 2<br>
        Email : info@veranta-soft.cz, Website : www.veranta-soft.cz<br>
        Phone : 1234567890 ; Fax : 1234567890
      </address>
    </div>
    <div class="foot"></div>
  </section>

  <section class="page page--front">
    <header class="masthead">
      <div class="brand"><span class="brand__dot"></span>Veranta</div>
      <div class="module">
        <span class="module__icon"></span>
      </div>
      <h1 class="module__name" style="top:122px;right:22px">MAJETEK</h1>
    </header>
    <div class="front-band"></div>
    <div class="screens">
      <div class="screens__item" role="img" aria-label="Snímek obrazovky modulu – přehled majetku"></div>
      <div class="screens__item" role="img" aria-label="Snímek obrazovky modulu – karta majetku"></div>
      <div class="screens__item" role="img" aria-label="Snímek obrazovky modulu – odpisy"></div>
      <div class="screens__item" role="img" aria-label="Snímek obrazovky modulu – sestavy"></div>
    </div>
    <div class="info">
      <div class="info__bar"><span class="info__label">Basic Info</span></div>
      <p class="info__text">Lorem ipsum dolor sit amet, consectetur adipisicing elit, sed do eiusmod tempor incididunt ut labore et dolore magna aliqua.</p>
      <div class="info__rule"></div>
      <p class="info__text">Lorem ipsum dolor sit amet, consectetur adipisicing elit, sed do eiusmod tempor incididunt ut labore et dolore magna aliqua. Ut enim ad minim veniam, quis nostrud exercitation ullamco laboris nisi ut aliquip ex ea commodo consequat.</p>
    </div>
    <div class="benefits">
      <h2 class="benefits__head">Co vam prinese <span class="benefits__icon" role="img" aria-label="Ilustrace modulu"></span></h2>
      <div class="benefits__line"></div>
      <ul class="benefits__list">
        <li><svg viewBox="0 0 9 10"><path d="M0 0L9 5L0 10Z"/></svg>Here will go key feature</li>
        <li><svg viewBox="0 0 9 10"><path d="M0 0L9 5L0 10Z"/></svg>Here will go key feature</li>
        <li><svg viewBox="0 0 9 10"><path d="M0 0L9 5L0 10Z"/></svg>Here will go key feature</li>
        <li><svg viewBox="0 0 9 10"><path d="M0 0L9 5L0 10Z"/></svg>Here will go key feature</li>
      </ul>
    </div>
    <div class="front-foot"></div>
  </section>

</main>
</body>
</html>
```